CalmPeak Nurses' Manifesto

Design a manifesto to inspire and motivate nurses to work at minimum standards of excellence in their nursing practice.

The manifesto will become a feature of our website, at conferences, workshops and retreats. It will also be featured on other marketing tools.

Primary Market:
Nurses and/or other healthcare professionals (specifically Doctors, Occupational Therapists, Psychologists and Social Workers).

However the manifesto is equally applicable to all nurses and healthcare professionals from new graduates to very experienced senior clinicians, administration officers,managers and healthcare executive personnel.

Mainly females and primarily 35 to 65 years old, which suggests people in this target age group have extensive experience, but have become jaded'.

The purpose of our business is to assist healthcare professionals, primarily nurses, to maintain their enthusiasm and excellence in service provision, for their benefit as well as the benefit of the clients.

I have attached:
File 1: Copy Samples and examples: which has the copy for the manifesto, examples that appeal to us and our 3 attempts.
File 2: Our colour Spec Sheet, HOWEVER the colours are not necessary limited to these colours. These colours are not in the logo that will be on the manifesto. The colours on the logo attached can/or also be used.
File 3: Prototype logo. The final logo will be available within 3 to 4 days.

Industry/Entity Type

Healthcare

Requirements
Must have
• Must use the copy as per the attached file.

It should be contemporary, eye catching and motivational.

Should not have
• MUST BE EASY TO READ. Each line MUST be clearly defined from each other.

```html
<!DOCTYPE html>
<html lang="en">
<head>
<meta charset="utf-8">
<title>CalmPeak Nurses' Manifesto</title>
<link rel="stylesheet" href="https://fonts.googleapis.com/css2?family=Alfa+Slab+One&display=swap">
<style>
  :root {
    --ink: #1f1f1f;
    --orange: #f5861f;
    --teal: #4dbfb6;
    --teal-edge: #1d2b2b;
    --paper-light: #ffffff;
    --paper-edge: #cfd0d2;
  }
  html, body {
    margin: 0;
    padding: 0;
    overflow: hidden;
  }
  body {
    width: 849px;
    height: 1200px;
    background: radial-gradient(ellipse at 50% 45%, var(--paper-light) 35%, var(--paper-edge) 100%);
  }
  .manifesto {
    display: block;
    width: 849px;
    height: 1200px;
    font-family: "Alfa Slab One", "Rockwell", serif;
  }
  .manifesto text { text-transform: uppercase; }
  .ink { fill: var(--ink); }
  .accent { fill: var(--orange); }
  .headline {
    fill: var(--teal);
    stroke: var(--teal-edge);
    stroke-width: 2.5;
    paint-order: stroke fill;
  }
  .manifesto .brand-name { fill: var(--ink); text-transform: none; }
  .manifesto .partner-name { fill: var(--teal); text-transform: none; }
  .partner-mark { fill: var(--teal); }
</style>
</head>
<body>
<svg class="manifesto" viewBox="0 0 849 1200" role="img" aria-label="CalmPeak Nurses' Manifesto">
  <!-- brand -->
  <circle class="partner-mark" cx="612" cy="82" r="9"/>
  <text class="brand-name" x="628" y="92" font-size="28">CalmPeak</text>

  <!-- opening -->
  <text class="headline" x="42" y="205" font-size="80" textLength="326" lengthAdjust="spacingAndGlyphs">Nurse</text>
  <text class="ink" x="388" y="168" font-size="24" textLength="150" lengthAdjust="spacingAndGlyphs">Look after</text>
  <text class="accent" x="388" y="225" font-size="57" textLength="255" lengthAdjust="spacingAndGlyphs">Yourself</text>
  <text class="ink" x="652" y="224" font-size="26" textLength="148" lengthAdjust="spacingAndGlyphs">&amp; value</text>
  <text class="ink" x="47" y="254" font-size="23" textLength="150" lengthAdjust="spacingAndGlyphs">With open</text>
  <text class="ink" x="204" y="254" font-size="34" textLength="163" lengthAdjust="spacingAndGlyphs">Hands,</text>
  <text class="ink" x="388" y="262" font-size="30" textLength="412" lengthAdjust="spacingAndGlyphs">Your health as much as you</text>
  <text class="ink" x="47" y="294" font-size="37" textLength="320" lengthAdjust="spacingAndGlyphs">Hearts &amp; Minds</text>
  <text class="ink" x="388" y="296" font-size="30" textLength="412" lengthAdjust="spacingAndGlyphs">Value the health of others.</text>

  <text class="ink" x="47" y="332" font-size="22" textLength="280" lengthAdjust="spacingAndGlyphs">Delight your clients &amp;</text>
  <text class="ink" x="47" y="355" font-size="22" textLength="366" lengthAdjust="spacingAndGlyphs">Colleagues by exceeding their</text>
  <text class="accent" x="420" y="355" font-size="63" textLength="380" lengthAdjust="spacingAndGlyphs">Expectations</text>

  <text class="ink" x="47" y="402" font-size="48" textLength="753" lengthAdjust="spacingAndGlyphs">Deliver care skillfully.</text>

  <text class="accent" x="47" y="450" font-size="45" textLength="218" lengthAdjust="spacingAndGlyphs">Respect</text>
  <text class="ink" x="275" y="450" font-size="18" textLength="138" lengthAdjust="spacingAndGlyphs">the limits of</text>
  <text class="ink" x="47" y="471" font-size="18" textLength="358" lengthAdjust="spacingAndGlyphs">People's knowledge &amp; share your</text>
  <text class="ink" x="47" y="490" font-size="18" textLength="230" lengthAdjust="spacingAndGlyphs">Knowledge generously.</text>

  <text class="accent" x="432" y="457" font-size="54" textLength="175" lengthAdjust="spacingAndGlyphs">Support</text>
  <text class="ink" x="617" y="437" font-size="23" textLength="183" lengthAdjust="spacingAndGlyphs">Your colleagues</text>
  <text class="ink" x="432" y="488" font-size="20" textLength="180" lengthAdjust="spacingAndGlyphs">&amp; champion their</text>
  <text class="accent" x="617" y="484" font-size="44" textLength="183" lengthAdjust="spacingAndGlyphs">Purpose.</text>

  <text class="accent" x="47" y="529" font-size="39" textLength="753" lengthAdjust="spacingAndGlyphs">Learn something new each day.</text>
  <text class="ink" x="47" y="556" font-size="18" textLength="753" lengthAdjust="spacingAndGlyphs">Trust your knowledge &amp; seek advice only from respected sources.</text>
  <text class="ink" x="47" y="604" font-size="51" textLength="753" lengthAdjust="spacingAndGlyphs">Be a lifelong learner.</text>
  <text class="accent" x="47" y="652" font-size="46" textLength="753" lengthAdjust="spacingAndGlyphs">Celebrate, respect &amp; value</text>
  <text class="ink" x="47" y="686" font-size="33" textLength="753" lengthAdjust="spacingAndGlyphs">The diversity of Australian culture.</text>

  <text class="accent" x="50" y="738" font-size="51" textLength="150" lengthAdjust="spacingAndGlyphs">Smile</text>
  <text class="ink" x="212" y="716" font-size="18" textLength="265" lengthAdjust="spacingAndGlyphs">&amp; infect others with</text>
  <text class="accent" x="302" y="735" font-size="18" textLength="54" lengthAdjust="spacingAndGlyphs">your</text>
  <text class="ink" x="47" y="766" font-size="35" textLength="405" lengthAdjust="spacingAndGlyphs">Happiness &amp; have fun!</text>

  <text class="accent" x="493" y="716" font-size="18" textLength="142" lengthAdjust="spacingAndGlyphs">Always do the</text>
  <text class="ink" x="640" y="742" font-size="58" textLength="160" lengthAdjust="spacingAndGlyphs">Right</text>
  <text class="ink" x="492" y="770" font-size="58" textLength="135" lengthAdjust="spacingAndGlyphs">Thing</text>
  <text class="accent" x="632" y="764" font-size="16" textLength="168" lengthAdjust="spacingAndGlyphs">without exception.</text>

  <text class="ink" x="47" y="798" font-size="20" textLength="190" lengthAdjust="spacingAndGlyphs">You are unique,</text>
  <text class="ink" x="88" y="818" font-size="20" textLength="145" lengthAdjust="spacingAndGlyphs">revel in your</text>
  <text class="accent" x="238" y="818" font-size="50" textLength="240" lengthAdjust="spacingAndGlyphs">Individuality.</text>
  <text class="ink" x="492" y="798" font-size="16" textLength="100" lengthAdjust="spacingAndGlyphs">Always be</text>
  <text class="accent" x="492" y="818" font-size="18" textLength="100" lengthAdjust="spacingAndGlyphs">focused.</text>
  <text class="ink" x="600" y="818" font-size="46" textLength="200" lengthAdjust="spacingAndGlyphs">Solution</text>

  <text class="accent" x="47" y="862" font-size="48" textLength="753" lengthAdjust="spacingAndGlyphs">Seek success firstly from within.</text>

  <text class="ink" x="47" y="892" font-size="20" textLength="375" lengthAdjust="spacingAndGlyphs">Only follow exceptional leaders.</text>
  <text class="accent" x="47" y="920" font-size="18" textLength="455" lengthAdjust="spacingAndGlyphs">If there is no one left to follow, then lead!</text>
  <text class="ink" x="565" y="888" font-size="20" textLength="235" lengthAdjust="spacingAndGlyphs">Always lead with</text>
  <text class="accent" x="588" y="910" font-size="20" textLength="212" lengthAdjust="spacingAndGlyphs">Purpose, passion</text>
  <text class="ink" x="588" y="932" font-size="20" textLength="212" lengthAdjust="spacingAndGlyphs">&amp; commitment.</text>

  <text class="ink" x="47" y="950" font-size="19" textLength="408" lengthAdjust="spacingAndGlyphs">Respond to complex situations innovatively,</text>
  <text class="ink" x="47" y="973" font-size="19" textLength="430" lengthAdjust="spacingAndGlyphs">creatively &amp; safely within the scope of</text>
  <text class="accent" x="488" y="973" font-size="41" textLength="312" lengthAdjust="spacingAndGlyphs">Your practice.</text>

  <text class="ink" x="47" y="1016" font-size="19" textLength="95" lengthAdjust="spacingAndGlyphs">Adopt a</text>
  <text class="accent" x="150" y="1018" font-size="44" textLength="195" lengthAdjust="spacingAndGlyphs">'Can do'</text>
  <text class="ink" x="47" y="1040" font-size="21" textLength="300" lengthAdjust="spacingAndGlyphs">attitude to everything</text>
  <text class="ink" x="80" y="1063" font-size="19" textLength="237" lengthAdjust="spacingAndGlyphs">that comes your way.</text>
  <text class="accent" x="365" y="1005" font-size="32" textLength="435" lengthAdjust="spacingAndGlyphs">Choose your thoughts wisely,</text>
  <text class="accent" x="365" y="1040" font-size="36" textLength="70" lengthAdjust="spacingAndGlyphs">they</text>
  <text class="ink" x="442" y="1040" font-size="36" textLength="358" lengthAdjust="spacingAndGlyphs">create your reality.</text>

  <text class="headline" x="333" y="1111" font-size="76" textLength="464" lengthAdjust="spacingAndGlyphs">Live your dream.</text>

  <!-- partner -->
  <rect class="partner-mark" x="52" y="1122" width="24" height="24"/>
  <text class="partner-name" x="86" y="1142" font-size="20">Care Growth Partners</text>
</svg>
</body>
</html>
```